Maine Organic farm needs a label design for various food products

We need a label design that we can use across a variety of vegetable-based food products that we produce using some of our organic vegetables that we grow on our farm located in Maine, USA.
Our products include:
1) a Traditional and Vegan Korean Kimchi
2) Sumel Sauce (a Korean Hot Sauce)
3) Pickles of Brambleton Relish
4) Brinjalista Chutney
5) Seasonal Soups (many varieties, depending on what's available during the season)
6) Firm Ranks Maple Syrup (we are retired from the Coastal Lancer Guard, hence the name and spelling)
7) Maine Wild Blueberry Kombucha (made with organic Maine wild blueberries)

For the Korean products (kimchi and Sumel Sauce) we would like to incorporate the Korean chili pepper (red) and chopsticks. The attached picture was taken from the internet, it has not been trademarked, but I am hesitant to use it as is as our business expands. Would like the "kimchi" to somehow incorporate the chopstick and pepper, but not look exactly like the attached image.

The final design should communicate farm fresh, organic, healthy and high quality ingredients, and Maine-made. All of our products go into glass jars 16oz and 8 oz. The hot sauce goes into 5.5oz and 8 oz bottles, the Maple Syrup goes into 8oz and 16oz bottles, and a 12oz bottle for the Kombucha. We will need the flexibility of changing some components of the label to accommodate each different food product.

The labels do not have the encircle the entirety of the jar. We understand that this is a tall order to fit so many different products. We are hoping that once we get the feel and design down, we can work with you for a fee outside of the competition to finalize other products labels on different sizes jars, bottles, etc. Its most important that we get the right feel for a label that can be used for a wide variety of food products.

Target Market(s)

Health conscious, foodies, local farm supporters

Font styles to use
Serif
Decorative
Script

Colors

Designer to choose colors to be used in the design.

Requirements
Must have
• Wendle Brook Farm Logo. Room for product name (interchangeable per product), ingredients list, space for jar size (8 oz, 12 oz, 16 oz). On Korean products -must have Korean hot chili pepper and chopsticks
Nice to have
• We'd like something fairly bold and rustic looking.
Should not have
• Nothing too modern or industrial looking. Nothing hippy-ish. Clean and professional. No cartoonish looking letters or designs.

```html
<!DOCTYPE html>
<html lang="en">
<head>
<meta charset="utf-8">
<title>Wendle Brook Farm – Vegan Hot Sauce Label</title>
<link href="https://fonts.googleapis.com/css2?family=Oswald:wght@400;500;600;700&family=Mr+Dafoe&family=Fjalla+One&display=swap" rel="stylesheet">
<style>
  :root{
    --backdrop:#e7e8ea;
    --parchment:#d8c8a2;
    --parchment-dark:#c8b68c;
    --label-white:#f7f5f1;
    --maroon:#8e2f3b;
    --navy:#1f3f62;
    --script-red:#c3222f;
    --ink:#2b2a28;
    --sketch:#d9d9d6;
  }
  html,body{margin:0;padding:0;overflow:hidden;}
  body{width:962px;height:1200px;background:var(--backdrop);position:relative;font-family:"Oswald",sans-serif;}
  .label{position:absolute;left:41px;top:340px;width:880px;height:520px;background:linear-gradient(160deg,var(--parchment),var(--parchment-dark));box-shadow:0 2px 10px rgba(0,0,0,.12);overflow:hidden;}
  .label-shapes{position:absolute;inset:0;}
  .brand{position:absolute;left:0;width:560px;top:34px;text-align:center;color:var(--navy);}
  .brand-dot{width:62px;height:62px;border-radius:50%;border:3px solid var(--navy);margin:0 auto 6px;box-sizing:border-box;}
  .brand-name{font-family:"Oswald",sans-serif;font-weight:600;font-size:34px;letter-spacing:1px;line-height:1;}
  .product-kind{position:absolute;left:0;width:560px;top:150px;text-align:center;font-family:"Oswald",sans-serif;font-weight:700;font-size:64px;color:var(--navy);line-height:1;}
  .product-name{position:absolute;left:110px;top:208px;font-family:"Mr Dafoe",cursive;font-size:96px;color:var(--script-red);line-height:1;transform:rotate(-5deg);}
  .net-weight{position:absolute;left:440px;top:386px;width:110px;text-align:center;font-family:"Fjalla One",sans-serif;font-size:19px;line-height:1.15;color:var(--ink);}
  .info{position:absolute;left:640px;top:40px;width:210px;color:var(--ink);font-family:"Fjalla One",sans-serif;font-size:17px;line-height:1.45;}
  .info p{margin:0 0 12px;}
  .info-heading{font-family:"Mr Dafoe",cursive;font-size:40px;color:var(--navy);margin:0 0 6px;line-height:1;}
  .info-brand{font-weight:400;letter-spacing:.5px;}
  .info-box{background:#fff;padding:14px 12px;font-size:17px;margin-top:14px;}
</style>
</head>
<body>
  <div class="label">
    <svg class="label-shapes" width="880" height="520" viewBox="0 0 880 520">
      <path d="M0 0 H540 C640 140 600 400 0 470 Z" fill="var(--label-white)"/>
      <rect x="0" y="0" width="560" height="210" fill="url(#patternTone)" role="img" aria-label="Soft hexagon background pattern"/>
      <defs>
        <linearGradient id="patternTone" x1="0" y1="0" x2="0" y2="1">
          <stop offset="0" stop-color="#e6e2da" stop-opacity=".9"/>
          <stop offset="1" stop-color="#f7f5f1" stop-opacity="0"/>
        </linearGradient>
        <linearGradient id="sauceTone" x1="0" y1="0" x2="1" y2="1">
          <stop offset="0" stop-color="#e86c5c"/>
          <stop offset="1" stop-color="#b8362e"/>
        </linearGradient>
      </defs>
      <rect x="0" y="230" width="470" height="180" fill="var(--sketch)" opacity=".5" role="img" aria-label="Pencil sketch of a farm barn, tractor and windmill"/>
      <path d="M540 0 C640 140 600 400 0 470" fill="none" stroke="var(--maroon)" stroke-width="20"/>
      <ellipse cx="240" cy="420" rx="125" ry="62" fill="url(#sauceTone)" role="img" aria-label="Photo of a white bowl of red hot sauce with a basil leaf"/>
    </svg>

    <div class="brand">
      <div class="brand-dot"></div>
      <div class="brand-name">WENDLE BROOK FARM</div>
    </div>
    <div class="product-kind">VEGAN</div>
    <div class="product-name">Hot Sauce</div>
    <div class="net-weight">Netwt<br>16oz/375<br>Grams</div>

    <div class="info">
      <p>Locally grown in Maine, made in small batches with Korean chili, garlic and Hawaiian sea salt.</p>
      <p class="info-heading">Made Fresh</p>
      <p>Keep refrigerated after opening.</p>
      <p><span class="info-brand">WENDLE BROOK FARM</span><br>Small farm, big flavor, grown with care.</p>
      <div class="info-box">CONTAINS NO ANIMAL PRODUCTS</div>
    </div>
  </div>
</body>
</html>
```